CFO services graphic design

I own a business consulting firm called Thornfield Advisory and we need a graphic for CFO services in our colours and branding. The attached file "CFO services to be put into Thornfield advisory theme", shows the content for the design. The two other files show the theme and colours for the new design.

```html
<!DOCTYPE html>
<html lang="en">
<head>
<meta charset="utf-8">
<title>Thornfield Advisory — CFO Services</title>
<link rel="stylesheet" href="https://fonts.googleapis.com/css2?family=Bebas+Neue&display=swap">
<style>
  :root {
    --forest-core: #0f2e24;
    --forest: #1d4d3c;
    --pine: #2a6b52;
    --teal: #2f8f6f;
    --sage: #7cc4a4;
    --gold: #c9a23a;
    --stone: #e8e6df;
    --white: #ffffff;
  }
  html, body {
    margin: 0;
    padding: 0;
    width: 1200px;
    height: 956px;
    overflow: hidden;
    background: var(--white);
  }
  .cfo-wheel {
    display: block;
    width: 1200px;
    height: 956px;
  }
  .service-label {
    font-family: "Bebas Neue", "Oswald", sans-serif;
    fill: var(--white);
    text-anchor: middle;
    font-size: 52px;
    letter-spacing: -0.5px;
    filter: drop-shadow(1px 2px 1px rgba(0,0,0,0.35));
  }
  .service-label.is-heading { font-size: 56px; }
  .service-label.is-detail { font-size: 29px; letter-spacing: -0.3px; }
  .core-label {
    font-family: "Bebas Neue", "Oswald", sans-serif;
    fill: var(--white);
    text-anchor: middle;
    font-size: 70px;
  }
  .brand-name {
    font-family: "Bebas Neue", "Oswald", sans-serif;
    fill: var(--forest);
    font-size: 44px;
    letter-spacing: 3px;
    text-anchor: middle;
  }
  .brand-mark { fill: var(--gold); }
  .petal { stroke: var(--stone); stroke-width: 6; stroke-linejoin: round; }
  .petal--teal { fill: var(--teal); }
  .petal--forest { fill: var(--forest); }
  .petal--pine { fill: var(--pine); }
  .petal--gold { fill: var(--gold); }
  .rim-segment { fill: none; stroke-width: 16; stroke-dasharray: 230 3578; }
  .rim--teal { stroke: var(--teal); }
  .rim--sage { stroke: var(--sage); }
  .rim--forest { stroke: var(--forest); }
  .rim--gold { stroke: var(--gold); }
  .spoke-arrow { stroke: var(--forest); fill: var(--forest); stroke-width: 6; }
</style>
</head>
<body>
<svg class="cfo-wheel" viewBox="0 0 2000 1594" xmlns="http://www.w3.org/2000/svg" role="img" aria-label="Thornfield Advisory Chief Financial Officer services wheel">
  <defs>
    <path id="petal-shape" d="M -220,-535 A 578 578 0 0 1 220,-535 L 130,-317 A 142 142 0 0 1 -130,-317 Z"/>
    <g id="spoke">
      <line x1="0" y1="-152" x2="0" y2="-186"/>
      <polygon points="-12,-184 12,-184 0,-220" stroke="none"/>
    </g>
  </defs>

  <g class="wheel" transform="translate(1000 797)">
    <g class="rim">
      <circle class="rim-segment rim--teal" r="606" transform="rotate(-112.1)"/>
      <circle class="rim-segment rim--gold" r="606" transform="rotate(-89.6)"/>
      <circle class="rim-segment rim--sage" r="606" transform="rotate(-67.1)"/>
      <circle class="rim-segment rim--forest" r="606" transform="rotate(-44.6)"/>
      <circle class="rim-segment rim--sage" r="606" transform="rotate(-22.1)"/>
      <circle class="rim-segment rim--forest" r="606" transform="rotate(0.4)"/>
      <circle class="rim-segment rim--teal" r="606" transform="rotate(22.9)"/>
      <circle class="rim-segment rim--forest" r="606" transform="rotate(45.4)"/>
      <circle class="rim-segment rim--teal" r="606" transform="rotate(67.9)"/>
      <circle class="rim-segment rim--gold" r="606" transform="rotate(90.4)"/>
      <circle class="rim-segment rim--sage" r="606" transform="rotate(112.9)"/>
      <circle class="rim-segment rim--forest" r="606" transform="rotate(135.4)"/>
      <circle class="rim-segment rim--sage" r="606" transform="rotate(157.9)"/>
      <circle class="rim-segment rim--forest" r="606" transform="rotate(180.4)"/>
      <circle class="rim-segment rim--sage" r="606" transform="rotate(202.9)"/>
      <circle class="rim-segment rim--forest" r="606" transform="rotate(225.4)"/>
    </g>

    <circle class="wheel-base" r="588" fill="#e8e6df"/>

    <g class="petals">
      <use href="#petal-shape" class="petal petal--teal"/>
      <use href="#petal-shape" class="petal petal--forest" transform="rotate(45)"/>
      <use href="#petal-shape" class="petal petal--gold" transform="rotate(90)"/>
      <use href="#petal-shape" class="petal petal--pine" transform="rotate(135)"/>
      <use href="#petal-shape" class="petal petal--teal" transform="rotate(180)"/>
      <use href="#petal-shape" class="petal petal--forest" transform="rotate(225)"/>
      <use href="#petal-shape" class="petal petal--gold" transform="rotate(270)"/>
      <use href="#petal-shape" class="petal petal--pine" transform="rotate(315)"/>
    </g>

    <g class="spoke-arrow">
      <use href="#spoke"/>
      <use href="#spoke" transform="rotate(45)"/>
      <use href="#spoke" transform="rotate(90)"/>
      <use href="#spoke" transform="rotate(135)"/>
      <use href="#spoke" transform="rotate(180)"/>
      <use href="#spoke" transform="rotate(225)"/>
      <use href="#spoke" transform="rotate(270)"/>
      <use href="#spoke" transform="rotate(315)"/>
    </g>

    <circle class="core" r="146" fill="#0f2e24"/>
  </g>

  <text class="core-label" x="1000" y="762">CHIEF</text>
  <text class="core-label" x="1000" y="820">FINANCIAL</text>
  <text class="core-label" x="1000" y="878">OFFICER</text>

  <g class="service cost-accounting">
    <text class="service-label" x="1000" y="312">COST</text>
    <text class="service-label" x="1000" y="360">ACCOUNTING &amp;</text>
    <text class="service-label" x="1000" y="408">COST</text>
    <text class="service-label" x="1000" y="457">MANAGEMENT</text>
  </g>
  <g class="service capital-structure">
    <text class="service-label" x="1296" y="438">CAPITAL</text>
    <text class="service-label" x="1296" y="486">STRUCTURE</text>
    <text class="service-label" x="1296" y="535">AND THE COST</text>
    <text class="service-label" x="1296" y="584">OF CAPITAL</text>
  </g>
  <g class="service investment-decisions">
    <text class="service-label" x="1430" y="742">LONG-TERM &amp;</text>
    <text class="service-label" x="1430" y="791">SHORT-TERM</text>
    <text class="service-label" x="1430" y="840">INVESTMENT</text>
    <text class="service-label" x="1430" y="889">DECISIONS</text>
  </g>
  <g class="service performance-evaluation">
    <text class="service-label" x="1308" y="1072">PERFORMANCE</text>
    <text class="service-label" x="1308" y="1120">EVALUATION</text>
  </g>
  <g class="service budgeting">
    <text class="service-label" x="1000" y="1224">BUDGETING &amp;</text>
    <text class="service-label" x="1000" y="1272">STRATEGIC PLANNING</text>
  </g>
  <g class="service risk-management">
    <text class="service-label" x="684" y="1072">RISK</text>
    <text class="service-label" x="684" y="1120">MANAGEMENT</text>
  </g>
  <g class="service compliance">
    <text class="service-label is-heading" x="577" y="767">COMPLIANCE:</text>
    <text class="service-label" x="577" y="817">TAX, LEGAL AND</text>
    <text class="service-label" x="577" y="866">REGULATORY</text>
  </g>
  <g class="service communication">
    <text class="service-label is-heading" x="688" y="491">COMMUNICATION</text>
    <text class="service-label is-detail" x="688" y="527">BOARD OF DIRECTORS,</text>
    <text class="service-label is-detail" x="688" y="557">CREDITORS, OWNERS, INVESTORS,</text>
    <text class="service-label is-detail" x="688" y="587">CREDIT RATING AGENCIES</text>
  </g>

  <g class="brand">
    <rect class="brand-mark" x="818" y="1482" width="22" height="22"/>
    <text class="brand-name" x="1012" y="1507">THORNFIELD ADVISORY</text>
  </g>
</svg>
</body>
</html>
```